Business Card Design needed for start up company Halvora

In need of a new business card designed for a start up company based in Sydney, Halvora is a new start up innovative Company, our mission it to make property accessible for everyday Australian and to become the leading Real Estate platform in Australia. We want it to be fresh and clean.

Industry/Entity Type

Financial

Contact Information for Business Card

Section for Name
Section for Title

HALVORA - The Strength of Pooling
Mobile:
Direct:

Font styles to use
Sans Serif

Colors
33a6d7
0692cd
0255a3
ffffff

Requirements
Must have
• Logo, all business card details

```html
<!DOCTYPE html>
<html lang="en">
<head>
<meta charset="utf-8">
<title>Halvora Business Card</title>
<link rel="stylesheet" href="https://fonts.googleapis.com/css2?family=Source+Sans+3:wght@400;600;800&display=swap">
<style>
  :root {
    --bg: #3a3432;
    --card: #141516;
    --card-edge: #1d1e20;
    --sky: #33a6d7;
    --azure: #0692cd;
    --navy: #0255a3;
    --white: #ffffff;
    --silver: #bfc1c3;
    --muted: #8e9093;
  }
  * { margin: 0; padding: 0; box-sizing: border-box; }
  html, body { width: 1200px; height: 864px; overflow: hidden; }
  body {
    background: var(--bg);
    font-family: "Source Sans 3", Arial, sans-serif;
    display: flex;
    flex-direction: column;
    align-items: center;
    justify-content: center;
    gap: 56px;
  }
  .card {
    position: relative;
    width: 600px;
    height: 343px;
    background: var(--card);
    border: 1px solid var(--card-edge);
    border-radius: 4px;
  }
  .brand {
    display: flex;
    align-items: center;
    gap: 12px;
  }
  .brand-dot {
    width: 54px;
    height: 54px;
    border-radius: 50%;
  }
  .brand-name {
    font-weight: 800;
    font-size: 50px;
    letter-spacing: 1px;
    line-height: 1;
  }

  /* front */
  .card-front .brand { position: absolute; left: 110px; top: 116px; }
  .card-front .brand-dot { background: var(--silver); }
  .card-front .brand-name { color: var(--silver); }
  .tagline {
    position: absolute;
    left: 112px;
    top: 206px;
    color: var(--muted);
    font-size: 15px;
  }

  /* back */
  .card-back .brand { position: absolute; left: 40px; top: 136px; }
  .card-back .brand-dot { background: var(--sky); }
  .card-back .brand-name { color: var(--navy); font-size: 44px; }
  .divider {
    position: absolute;
    left: 348px;
    top: 64px;
    width: 1px;
    height: 215px;
    background: linear-gradient(to bottom, transparent, var(--silver) 30%, var(--silver) 70%, transparent);
  }
  .details {
    position: absolute;
    left: 372px;
    top: 74px;
    color: var(--white);
    font-size: 15px;
    line-height: 21px;
  }
  .person-name { color: var(--navy); font-weight: 600; font-size: 16px; letter-spacing: .5px; }
  .person-title { color: var(--azure); font-weight: 600; font-size: 16px; letter-spacing: .5px; margin-bottom: 8px; }
  .contact-line { display: flex; align-items: center; gap: 8px; }
  .contact-line svg { width: 12px; height: 12px; fill: var(--silver); flex: none; }
  .spacer { width: 12px; flex: none; }
</style>
</head>
<body>
  <section class="card card-front">
    <div class="brand">
      <span class="brand-dot"></span>
      <span class="brand-name">HALVORA</span>
    </div>
    <p class="tagline">The Strength of Pooling</p>
  </section>

  <section class="card card-back">
    <div class="brand">
      <span class="brand-dot"></span>
      <span class="brand-name">HALVORA</span>
    </div>
    <span class="divider"></span>
    <div class="details">
      <p class="person-name">MARCUS REILLY</p>
      <p class="person-title">CEO/FOUNDER</p>
      <p class="contact-line"><span class="spacer"></span>42 Kellmore Street</p>
      <p class="contact-line"><span class="spacer"></span>Sydney, NSW 2000</p>
      <p class="contact-line">
        <svg viewBox="0 0 12 12"><path d="M1 4c0-2 2-3 5-3s5 1 5 3l-2 1-1-2H4L3 5 1 4zM2 6h8l1 5H1z"/></svg>
        02 8145 3306
      </p>
      <p class="contact-line">
        <svg viewBox="0 0 12 12"><path d="M3 0h6v12H3zM4 1.5v8h4v-8z"/></svg>
        0412 775 902
      </p>
      <p class="contact-line">
        <svg viewBox="0 0 12 12"><path d="M0 2h12v8H0zM1 3l5 4 5-4z"/></svg>
        marcus@halvora.com
      </p>
      <p class="contact-line">
        <svg viewBox="0 0 12 12"><circle cx="6" cy="6" r="6"/></svg>
        www.halvora.com
      </p>
    </div>
  </section>
</body>
</html>
```